A-Stand Directional Sign Design

Objective:
We need a professional graphic design for an A-Stand sign that will guide customers arriving in our parking lot to our office. The design should be visually clear, welcoming, and aligned with our brand identity.
REQUIREMENTS:
Two versions of the design:
- One with an arrow pointing left
- One with an arrow pointing right
(This allows us to place the A-Stand anywhere and flip the graphic as needed.)
DIMENSIONS:
- Viewable Area: 30" x 40"
BRAND ALIGNMENT:
- Colors, fonts, and overall style should match our website: www.glidemarrow.com
- Clean, modern, and professional look consistent with our aviation/tourism brand
CONTENT:
- Clear directional arrow (left or right depending on version)
- Text: “Office Entrance” or similar concise wording (designers may propose alternatives if they improve clarity)
READABILITY:
- Bold, high-contrast design for visibility from a distance
- Simple layout that avoids clutter
DELIVERABLES:
- Final artwork in print-ready format (PDF preferred)
- Two versions: Arrow Left and Arrow Right
DESIGN GOAL:
Ensure customers can easily find our office upon arrival, while reinforcing glideMARROW’s professional and welcoming brand image.
Target Market(s)
Tourism
Look and feel

```html
<!DOCTYPE html>
<html lang="en">
<head>
<meta charset="utf-8">
<title>glideMARROW A-Stand Directional Signs</title>
<link rel="stylesheet" href="https://fonts.googleapis.com/css2?family=Noto+Sans:wght@400;700;800&display=swap">
<style>
  :root {
    --page-bg: #f2f2f3;
    --sign-top: #2b2f37;
    --sign-mid: #0b0c0e;
    --sign-bottom: #1b1d22;
    --ink-white: #ffffff;
    --arrow-blue: #0a6ef2;
    --arrow-blue-deep: #0b4fc4;
    --sign-shadow: rgba(0, 0, 0, 0.18);
  }
  * { box-sizing: border-box; margin: 0; padding: 0; }
  html, body {
    width: 929px;
    height: 1200px;
    overflow: hidden;
    background: var(--page-bg);
    font-family: "Noto Sans", Verdana, sans-serif;
  }
  .sign-sheet {
    position: relative;
    width: 929px;
    height: 1200px;
    display: grid;
    grid-template-columns: 400px 400px;
    grid-template-rows: 533px 533px;
    column-gap: 49px;
    row-gap: 54px;
    padding: 40px 40px;
  }
  .sign {
    position: relative;
    width: 400px;
    height: 533px;
    overflow: hidden;
    background: linear-gradient(180deg, var(--sign-top) 0%, var(--sign-mid) 55%, var(--sign-mid) 80%, var(--sign-bottom) 100%);
    box-shadow: 0 6px 18px var(--sign-shadow);
    color: var(--ink-white);
  }
  .brand {
    position: absolute;
    top: 40px;
    left: 0;
    right: 0;
    display: flex;
    justify-content: center;
    align-items: center;
    gap: 10px;
  }
  .brand-dot {
    width: 14px;
    height: 14px;
    border-radius: 50%;
    background: var(--ink-white);
  }
  .brand-name {
    font-size: 28px;
    font-weight: 700;
    letter-spacing: 0.5px;
    color: var(--ink-white);
  }
  .photo {
    position: absolute;
    top: 95px;
    left: 10px;
    right: 10px;
    height: 178px;
    border-radius: 50% 50% 0 0 / 34px 34px 0 0;
  }
  .photo::after {
    content: "";
    position: absolute;
    inset: 0;
    border-radius: inherit;
    background: linear-gradient(180deg, rgba(11,12,14,0) 55%, var(--sign-mid) 100%);
  }
  .photo--pilot-city {
    background: linear-gradient(160deg, #dfe6ee 0%, #8a99ab 35%, #3f4a57 70%, #1c2026 100%);
  }
  .photo--group-selfie {
    background: linear-gradient(160deg, #cfe3e6 0%, #3e8f7c 30%, #2c3a58 60%, #5e6a8c 100%);
  }
  .photo--cockpit-coast {
    background: linear-gradient(160deg, #5b3b30 0%, #4f7e8c 30%, #2f5f6e 60%, #1a2a31 100%);
  }
  .photo--aerial-bay {
    background: linear-gradient(170deg, #e8eef3 0%, #8fa9bf 30%, #1f9a86 60%, #2a3f5a 100%);
  }
  .headline {
    position: absolute;
    top: 278px;
    left: 0;
    right: 0;
    text-align: center;
    font-size: 33px;
    font-weight: 800;
    line-height: 1.13;
  }
  .headline-small {
    font-size: 24px;
  }
  .tagline {
    position: absolute;
    top: 400px;
    left: 0;
    right: 0;
    text-align: center;
    font-size: 15px;
    font-weight: 700;
  }
  .entrance-arrow {
    position: absolute;
    top: 436px;
    width: 352px;
    height: 60px;
    display: flex;
    align-items: center;
    background: linear-gradient(90deg, var(--arrow-blue) 0%, var(--arrow-blue) 60%, var(--arrow-blue-deep) 100%);
    font-size: 23px;
    font-weight: 800;
    color: var(--ink-white);
  }
  .entrance-arrow--right {
    left: 26px;
    padding-left: 24px;
    clip-path: polygon(0 18%, 89% 18%, 89% 0, 100% 50%, 89% 100%, 89% 82%, 0 82%);
  }
  .entrance-arrow--left {
    left: 22px;
    padding-left: 54px;
    background: linear-gradient(90deg, var(--arrow-blue-deep) 0%, var(--arrow-blue) 35%, var(--arrow-blue) 100%);
    clip-path: polygon(0 50%, 11% 0, 11% 18%, 100% 18%, 100% 82%, 11% 82%, 11% 100%);
  }
</style>
</head>
<body>
<main class="sign-sheet">

  <section class="sign sign--right">
    <div class="brand"><span class="brand-dot"></span><span class="brand-name">glideMARROW</span></div>
    <div class="photo photo--pilot-city" role="img" aria-label="Photo from inside a helicopter cockpit: pilot with headset flying over a city skyline"></div>
    <h2 class="headline">The ULTIMATE<br>Helicopter<br>Experience</h2>
    <p class="tagline">Say Yes to new Adventures.</p>
    <div class="entrance-arrow entrance-arrow--right">Office Entrance</div>
  </section>

  <section class="sign sign--left">
    <div class="brand"><span class="brand-dot"></span><span class="brand-name">glideMARROW</span></div>
    <div class="photo photo--group-selfie" role="img" aria-label="Photo of smiling passengers with headsets taking a selfie inside a helicopter above a green coastline"></div>
    <h2 class="headline">ELEVATE<br>Your Helicopter<br>Experience</h2>
    <p class="tagline">We create memories.</p>
    <div class="entrance-arrow entrance-arrow--left">Office Entrance</div>
  </section>

  <section class="sign sign--right">
    <div class="brand"><span class="brand-dot"></span><span class="brand-name">glideMARROW</span></div>
    <div class="photo photo--cockpit-coast" role="img" aria-label="Photo of pilot and passenger with headsets in a helicopter cockpit flying over a coastal island"></div>
    <h2 class="headline"><span class="headline-small">The</span> NEXT LEVEL<br>Helicopter<br>Experience</h2>
    <p class="tagline">Say Yes to new Adventures.</p>
    <div class="entrance-arrow entrance-arrow--right">Office Entrance</div>
  </section>

  <section class="sign sign--left">
    <div class="brand"><span class="brand-dot"></span><span class="brand-name">glideMARROW</span></div>
    <div class="photo photo--aerial-bay" role="img" aria-label="Aerial photo from an open helicopter door over a turquoise bay and waterfront city"></div>
    <h2 class="headline">A PREMIUM<br>Helicopter<br>Experience</h2>
    <p class="tagline">We create memories.</p>
    <div class="entrance-arrow entrance-arrow--left">Office Entrance</div>
  </section>

</main>
</body>
</html>
```